Commercial Rooftop Solar business needs a website

We need a website with fantastic appeal for a new company based in Melbourne called Tallow Ridge Energy. We design and install solar energy systems for commercial applications across Australia. Our market is to focus on small to medium businesses looking for solar solutions, but we will also provide our service for residential customers. We would like a beautiful 'front page' feel to our home page, using photographs of solar PV systems and/or natural imagery. Our logo uses the colours orange and black, which could easily be echoed in photographic imagery of sunset and sunrise, for example. The design should communicate quiet confidence and professionalism to a corporate marketplace.

NEW POINTS FOR BRIEF: This design also needs to be flexible to allow for additional future content, including a Support page with sub pages, FAQ's, and a Blog.

As part of this design project, we will require the coding for the website to be completed by the designer.

We have seen some websites, which we like the look and feel of: these are listed below.

brightvanepower.com.au:

• Beautiful images underlaying brief text selling points.
• Simple ‘front cover’ style home page with elegant drop-down menu, stylish simple font style.
• Home page invites exploration through the menu links, rather than trying to provide all the information up front.
• Company logo and name in the top left hand corner, contact details accessible at top right hand, seems consistent in most sites.

kelpworks.com.au

rumbofield.com:
• Same element as the others is the front-page style home page with beautiful images underlying text.

We have a webpage that we started uploading content to. You can use some of the content there in your designs: www.tallowridgeenergy.com.au

Technical Specifications:
PAGES:

Home

About Us

Solutions - Commercial
- Residential

Products - Solar Panels - Vorla Heron, Vorla TELD, Vorla QB
- Solar Inverters - Kestamo, BrilQuill
- Monitoring systems - Dunmere Metrics
- Batteries - RW

- Datasheets have been provided for reference but if it's too much work, you can use generic text and we will provide content later.

Contact Us

FUTURE PAGES (Please consider in structure, where links could be placed):

Support

FAQ's

Blog.

We could provide some content for the Support page soon, but the Blog and FAQ's are future pages which we don't want highlighted in the design as we don't yet have content.

Phone: 1800 7 BIRCH
Email: sales@tallowridgeenergy.com.au

Currently, I do not have images and text available. Please
use placeholders in the meantime. The final text and images will be uploaded for the winner once a winning design has been selected.

Target Market(s)

Primary focus is on small to medium sized business owners. Those owners will have a house which may be suitable for solar so we want to cater to residential deeper in the website.

Industry/Entity Type

Solar Energy

Coding

Coded - Design and coding required

Number of Pages Required

5+ page

Colors
f78f20
0255a3

Requirements
Must have
• Logo as per attachments.
Nice to have
• Logo can have alternate colours Eg. White on Orange or Black etc. provided colour correct logo is shown somewhere eg. footer or contact page.
• In the active site, I'd like to have:
• Very slowly zooming images - barely perceptible.
• Title text that rolls into place
• Subtle movements
• See https://plumtally.com.au/ for example

```html
<!DOCTYPE html>
<html lang="en">
<head>
<meta charset="utf-8">
<title>Tallow Ridge Energy</title>
<link rel="stylesheet" href="https://fonts.googleapis.com/css2?family=Open+Sans:wght@400;600;700&family=Raleway:wght@500;600;700;800&display=swap">
<style>
:root{
  --orange:#f05a22;
  --ink:#222222;
  --text:#666666;
  --muted:#888888;
  --line:#dddddd;
  --grey-bg:#f6f6f6;
  --footer:#1d1d1d;
  --white:#ffffff;
}
*{box-sizing:border-box;margin:0;padding:0}
html,body{width:1200px;height:2667px;overflow:hidden}
body{font-family:"Open Sans",sans-serif;color:var(--text);background:var(--white);position:relative}
.heading{font-family:"Raleway",sans-serif;font-weight:800;color:var(--ink);text-transform:uppercase}
.rule{display:block;width:80px;height:3px;background:var(--orange)}

/* hero */
.hero{position:absolute;left:0;top:0;width:1200px;height:571px;overflow:hidden}
.hero-photo{position:absolute;inset:0;background:
  radial-gradient(ellipse 420px 260px at 600px 420px,#f7c46a 0%,#e88a3a 30%,rgba(120,70,50,0) 75%),
  linear-gradient(180deg,#2c3644 0%,#4b4a52 35%,#8a6448 60%,#3c3a2a 82%,#3e5a22 100%)}
.nav{position:absolute;top:0;left:0;width:1200px;height:118px}
.brand{position:absolute;left:75px;top:40px;display:flex;align-items:center;gap:12px;color:var(--white);font-family:"Raleway",sans-serif;font-weight:700;font-size:24px}
.brand-dot{width:30px;height:30px;border-radius:50%;background:var(--white)}
.menu{position:absolute;left:446px;top:48px;display:flex;gap:30px;list-style:none;font-family:"Raleway",sans-serif;font-weight:700;font-size:15px;color:var(--white)}
.menu .active{color:var(--orange)}
.menu .caret{display:inline-block;margin-left:6px;border:5px solid transparent;border-top-color:var(--white);transform:translateY(3px)}
.search{position:absolute;left:890px;top:50px}
.call{position:absolute;left:948px;top:44px;display:flex;align-items:center;gap:10px;color:var(--white);font-weight:600;font-size:16px}
.call-badge{width:28px;height:28px;border-radius:50%;background:var(--orange);display:flex;align-items:center;justify-content:center}
.hero-copy{position:absolute;left:0;top:168px;width:1200px;text-align:center;color:var(--white)}
.hero-title{font-weight:700;font-size:60px;letter-spacing:1px;text-shadow:0 2px 6px rgba(0,0,0,.35)}
.hero-sub{margin:22px auto 0;width:720px;font-size:24px;line-height:36px;font-weight:600;text-shadow:0 2px 4px rgba(0,0,0,.4)}
.btn-primary{display:inline-block;margin-top:34px;background:var(--orange);color:var(--white);font-weight:700;font-size:16px;padding:13px 32px;border:2px solid #ff8a5a;border-radius:3px}
.scroll-cue{position:absolute;left:584px;top:484px}
.slide-arrow{position:absolute;top:272px}

/* welcome */
.welcome{position:absolute;left:0;top:571px;width:1200px;height:590px;text-align:center}
.welcome .heading{margin-top:80px;font-size:34px}
.welcome .rule{margin:22px auto 0}
.intro{margin:36px auto 0;width:760px;font-size:12.5px;line-height:24px;color:var(--muted)}
.features{position:absolute;left:98px;top:280px;width:1020px;display:grid;grid-template-columns:repeat(3,357px);row-gap:60px;text-align:left}
.feature{display:flex;gap:20px}
.feature-icon{flex:none;width:78px;height:78px;border-radius:50%;border:1px solid #cfcfcf;display:flex;align-items:center;justify-content:center}
.feature h3{font-family:"Raleway",sans-serif;font-weight:600;font-size:19px;color:var(--ink);margin-top:6px}
.feature p{margin-top:12px;font-size:12.5px;line-height:24px;color:var(--muted);width:200px}

/* solutions */
.solutions{position:absolute;left:0;top:1160px;width:1200px;height:783px;background:var(--grey-bg)}
.solutions>.heading{text-align:center;margin-top:60px;font-size:34px}
.solution{position:absolute;top:174px;width:474px}
.solution-photo{height:262px;border:6px solid var(--white);box-shadow:0 0 0 1px #e2e2e2}
.photo-field{background:linear-gradient(180deg,#f0a140 0%,#f6c36a 28%,#e0733a 42%,#9a4c50 60%,#b45a60 100%)}
.photo-roof{background:linear-gradient(180deg,#c9b690 0%,#b8b7a4 30%,#8f9aa8 55%,#3d3f44 80%,#2a2c30 100%)}
.solution h3{margin-top:40px;font-family:"Raleway",sans-serif;font-weight:700;font-size:26px;color:var(--ink)}
.solution .rule{margin-top:14px;width:60px;height:2px}
.solution p{margin-top:28px;font-size:13px;line-height:25px;color:var(--muted)}
.btn-outline{display:inline-block;margin-top:26px;border:1px solid #bdbdbd;border-radius:4px;padding:10px 13px;font-size:12px;font-weight:700;color:var(--orange);background:var(--white)}

/* products */
.products{position:absolute;left:0;top:1943px;width:1200px;height:347px;text-align:center}
.products .heading{margin-top:64px;font-size:34px}
.products .rule{margin:20px auto 0}
.brands{position:absolute;left:98px;top:175px;display:flex;gap:29px}
.brand-tile{width:178px;height:86px;border:3px solid #e6e6e6;background:var(--white);display:flex;align-items:center;justify-content:center;font-family:"Raleway",sans-serif;font-weight:600;font-size:24px;color:#8c8c8c}

/* footer */
.footer{position:absolute;left:0;top:2290px;width:1200px;height:377px;background:var(--footer);border-top:4px solid var(--orange);color:#cfcfcf}
.footer-brand{position:absolute;left:98px;top:100px;display:flex;align-items:center;gap:10px;color:var(--white);font-family:"Raleway",sans-serif;font-weight:700;font-size:19px;width:180px;line-height:24px}
.footer-brand .brand-dot{width:26px;height:26px;flex:none}
.footer h4{font-family:"Raleway",sans-serif;font-weight:700;font-size:16px;color:var(--white);text-transform:uppercase}
.col-contact{position:absolute;left:310px;top:56px}
.contact-list{list-style:none;margin-top:26px;font-size:12.5px;line-height:20px}
.contact-list li{display:flex;gap:14px;margin-bottom:14px}
.col-signup{position:absolute;left:622px;top:56px;width:290px}
.col-signup p{margin-top:18px;font-size:11.5px;line-height:19px}
.email-field{margin-top:14px;width:284px;height:40px;background:var(--white);color:#555;font-size:11px;padding:12px}
.btn-subscribe{margin-top:16px;display:inline-block;background:var(--orange);color:var(--white);font-size:13px;font-weight:700;padding:12px 16px}
.col-links{position:absolute;left:985px;top:56px}
.col-links ul{list-style:none;margin-top:26px;font-size:12px;line-height:24px;color:var(--white)}
.copyright{position:absolute;left:0;top:300px;width:1200px;text-align:center;font-size:12px;color:#e0e0e0}
</style>
</head>
<body>

<header class="hero">
  <div class="hero-photo" role="img" aria-label="Sunset over rows of solar panels with a power pylon and wind turbines"></div>
  <nav class="nav">
    <div class="brand"><span class="brand-dot"></span>Tallow Ridge Energy</div>
    <ul class="menu">
      <li class="active">HOME</li>
      <li>ABOUT US</li>
      <li>SOLUTIONS<span class="caret"></span></li>
      <li>CONTACT US</li>
    </ul>
    <svg class="search" width="16" height="16" viewBox="0 0 16 16"><circle cx="6.5" cy="6.5" r="4.5" fill="none" stroke="#fff" stroke-width="2"/><line x1="10" y1="10" x2="14" y2="14" stroke="#fff" stroke-width="2.2" stroke-linecap="round"/></svg>
    <div class="call">
      <span class="call-badge"><svg width="14" height="14" viewBox="0 0 24 24"><path d="M6.6 10.8a15 15 0 006.6 6.6l2.2-2.2c.3-.3.7-.4 1-.2 1.1.4 2.3.6 3.6.6.6 0 1 .4 1 1V20c0 .6-.4 1-1 1A17 17 0 013 4c0-.6.4-1 1-1h3.5c.6 0 1 .4 1 1 0 1.3.2 2.5.6 3.6.1.3 0 .7-.2 1z" fill="#fff"/></svg></span>
      1 800 555 0142
    </div>
  </nav>
  <svg class="slide-arrow" style="left:12px" width="14" height="22" viewBox="0 0 14 22"><polyline points="11,2 3,11 11,20" fill="none" stroke="#fff" stroke-width="2"/></svg>
  <svg class="slide-arrow" style="left:1174px" width="14" height="22" viewBox="0 0 14 22"><polyline points="3,2 11,11 3,20" fill="none" stroke="#fff" stroke-width="2"/></svg>
  <div class="hero-copy">
    <h1 class="hero-title">TALLOW RIDGE ENERGY</h1>
    <p class="hero-sub">We design and install solar energy systems for commercial applications across Australia</p>
    <span class="btn-primary">GET MORE INFO</span>
  </div>
  <svg class="scroll-cue" width="32" height="46" viewBox="0 0 32 46"><rect x="1" y="1" width="30" height="44" rx="15" fill="none" stroke="#fff" stroke-width="2"/><polyline points="10,15 16,21 22,15" fill="none" stroke="#fff" stroke-width="2"/><polyline points="10,23 16,29 22,23" fill="none" stroke="#fff" stroke-width="2"/></svg>
</header>

<section class="welcome">
  <h2 class="heading">Welcome to Tallow Ridge Energy</h2>
  <span class="rule"></span>
  <p class="intro">Nemo enim ipsam voluptatem quia voluptas sit aspernatur aut odit aut fugit, sed quia consequuntur magni dolores eos qui ratione voluptatem sequi nesi dolorem ipsum quia dolor sit amet, consectetur, adipisci velit, sed quiauam</p>
  <div class="features">
    <div class="feature">
      <span class="feature-icon"><svg width="32" height="32" viewBox="0 0 32 32"><rect x="4" y="8" width="20" height="20" rx="3" fill="none" stroke="var(--orange)" stroke-width="2.5"/><path d="M14 20l2-6 11-11 4 4-11 11z" fill="var(--orange)"/></svg></span>
      <div><h3>System Design</h3><p>At vero eos et accusamus et iusto odio dignissimos ducim</p></div>
    </div>
    <div class="feature">
      <span class="feature-icon"><svg width="34" height="34" viewBox="0 0 34 34"><circle cx="13" cy="19" r="8" fill="none" stroke="var(--orange)" stroke-width="5" stroke-dasharray="3 2.3"/><circle cx="13" cy="19" r="3" fill="var(--orange)"/><circle cx="25" cy="9" r="5" fill="none" stroke="var(--orange)" stroke-width="4" stroke-dasharray="2.5 1.5"/><circle cx="25" cy="26" r="4" fill="none" stroke="var(--orange)" stroke-width="3.5" stroke-dasharray="2 1.4"/></svg></span>
      <div><h3>Operational Management</h3><p>At vero eos et accusamus et iusto odio dignissimos ducim</p></div>
    </div>
    <div class="feature">
      <span class="feature-icon"><svg width="32" height="32" viewBox="0 0 32 32"><path d="M26 4a7 7 0 00-8.6 9L5 25.4 8.6 29 21 16.6A7 7 0 0030 8l-4 4-4-1-1-4z" fill="var(--orange)"/></svg></span>
      <div><h3>Installation</h3><p>At vero eos et accusamus et iusto odio dignissimos ducim</p></div>
    </div>
    <div class="feature">
      <span class="feature-icon"><svg width="34" height="34" viewBox="0 0 34 34"><g stroke="var(--orange)" stroke-width="2.5"><line x1="17" y1="2" x2="17" y2="7"/><line x1="17" y1="27" x2="17" y2="32"/><line x1="2" y1="17" x2="7" y2="17"/><line x1="27" y1="17" x2="32" y2="17"/><line x1="6" y1="6" x2="9.5" y2="9.5"/><line x1="24.5" y1="24.5" x2="28" y2="28"/><line x1="28" y1="6" x2="24.5" y2="9.5"/><line x1="6" y1="28" x2="9.5" y2="24.5"/></g><circle cx="17" cy="17" r="8" fill="var(--orange)"/><path d="M18 11l-5 7h4l-1 5 5-7h-4z" fill="#fff"/></svg></span>
      <div><h3>Solar Irrigation</h3><p>At vero eos et accusamus et iusto odio dignissimos ducim</p></div>
    </div>
    <div class="feature">
      <span class="feature-icon"><svg width="36" height="24" viewBox="0 0 36 24"><rect x="2" y="3" width="29" height="18" rx="2" fill="none" stroke="var(--orange)" stroke-width="2.5"/><rect x="31" y="8" width="3" height="8" fill="var(--orange)"/><rect x="6" y="7" width="21" height="10" fill="var(--orange)"/></svg></span>
      <div><h3>Energy Storage</h3><p>At vero eos et accusamus et iusto odio dignissimos ducim</p></div>
    </div>
    <div class="feature">
      <span class="feature-icon"><svg width="26" height="34" viewBox="0 0 26 34"><path d="M13 2a10 10 0 00-6 18c1 1 2 2 2 4h8c0-2 1-3 2-4a10 10 0 00-6-18z" fill="none" stroke="var(--orange)" stroke-width="2.5"/><rect x="9" y="26" width="8" height="2.5" fill="var(--orange)"/><rect x="10" y="30" width="6" height="2.5" fill="var(--orange)"/></svg></span>
      <div><h3>Feasibility Study</h3><p>At vero eos et accusamus et iusto odio dignissimos ducim</p></div>
    </div>
  </div>
</section>

<section class="solutions">
  <h2 class="heading">Our Solutions</h2>
  <article class="solution" style="left:98px">
    <div class="solution-photo photo-field" role="img" aria-label="Field of solar panels under a setting sun"></div>
    <h3>COMMERCIAL</h3>
    <span class="rule"></span>
    <p>Nam libero tempore, cum soluta nobis est eligendi optio cumque nihil impdit quo minus id quod maxime placeat facere possimus, omnis voluptas amenda est, omnis dolor repellendus et voluptates repudi earum rerum hic tenetur sa piente delectus, ut aut rei voluptatib.</p>
    <span class="btn-outline">READ MORE &gt;&gt;</span>
  </article>
  <article class="solution" style="left:628px">
    <div class="solution-photo photo-roof" role="img" aria-label="Solar panels mounted on a shingled house roof"></div>
    <h3>RESIDENTIAL</h3>
    <span class="rule"></span>
    <p>Nam libero tempore, cum soluta nobis est eligendi optio cumque nihil impdit quo minus id quod maxime placeat facere possimus, omnis voluptas amenda est, omnis dolor repellendus et voluptates repudi earum rerum hic tenetur sa piente delectus, ut aut rei voluptatib.</p>
    <span class="btn-outline">READ MORE &gt;&gt;</span>
  </article>
</section>

<section class="products">
  <h2 class="heading">Our Products</h2>
  <span class="rule"></span>
  <div class="brands">
    <div class="brand-tile">Rondel</div>
    <div class="brand-tile">Ambrato</div>
    <div class="brand-tile">Qilvane</div>
    <div class="brand-tile">Setmarrow</div>
    <div class="brand-tile">Learnwick</div>
  </div>
</section>

<footer class="footer">
  <div class="footer-brand"><span class="brand-dot"></span>Tallow Ridge Energy</div>
  <div class="col-contact">
    <h4>Contact Us</h4>
    <ul class="contact-list">
      <li><svg width="14" height="18" viewBox="0 0 14 18"><path d="M7 1a6 6 0 00-6 6c0 4.5 6 10 6 10s6-5.5 6-10a6 6 0 00-6-6z" fill="none" stroke="#ddd" stroke-width="1.4"/><circle cx="7" cy="7" r="2" fill="none" stroke="#ddd" stroke-width="1.4"/></svg><span>Tallow Ridge Energy<br>Harlow Vale, Fenbrook, Wessford.</span></li>
      <li><svg width="16" height="16" viewBox="0 0 24 24"><path d="M6.6 10.8a15 15 0 006.6 6.6l2.2-2.2c.3-.3.7-.4 1-.2 1.1.4 2.3.6 3.6.6.6 0 1 .4 1 1V20c0 .6-.4 1-1 1A17 17 0 013 4c0-.6.4-1 1-1h3.5c.6 0 1 .4 1 1 0 1.3.2 2.5.6 3.6.1.3 0 .7-.2 1z" fill="none" stroke="#ddd" stroke-width="1.6"/></svg><span>Phone : +44(0)20 5550 1287</span></li>
      <li><svg width="16" height="14" viewBox="0 0 16 14"><rect x="1" y="2" width="14" height="10" fill="none" stroke="#ddd" stroke-width="1.3"/><polyline points="1,2 8,8 15,2" fill="none" stroke="#ddd" stroke-width="1.3"/></svg><span>admin@tallowridgeenergy.com.au</span></li>
    </ul>
  </div>
  <div class="col-signup">
    <h4>Sign up to receive email</h4>
    <p>Excepteur sint occaecat cupidatat non proident, sunt in culpa qui Nemo enim ipsam voluptatem</p>
    <div class="email-field">Enter Email</div>
    <span class="btn-subscribe">SUBSCRIBE</span>
  </div>
  <div class="col-links">
    <h4>Quick Links</h4>
    <ul>
      <li>Home</li><li>About Us</li><li>Solutions</li><li>Projects</li><li>Blog</li><li>Contact Us</li>
    </ul>
  </div>
  <p class="copyright">Copyright © Tallow Ridge Energy 2017. All rights reserved.</p>
</footer>

</body>
</html>
```